Business card for a new cabinet shop company named Veloran Cabinets for high end cabinets

Design a business card, thinking dark rich green with colours to speak of high end luxury ie; cream, gold, black possibly

Mitchell Tarrowby
Director Craftsman
Email: info@veloranjoinery-example.com.au
Instagram : @veloran.cabinets

```html
<!DOCTYPE html>
<html lang="en">
<head>
<meta charset="utf-8">
<title>Veloran Cabinets – Business Card</title>
<link rel="stylesheet" href="https://fonts.googleapis.com/css2?family=Poppins:wght@300&family=Open+Sans:wght@400;600;800&display=swap">
<style>
  :root {
    --backdrop: #151816;
    --card-green: #173a2c;
    --card-green-ink: #24503e;
    --card-cream: #f8f4ea;
    --ink: #111111;
    --gold: #c9a24a;
  }
  * { box-sizing: border-box; margin: 0; padding: 0; }
  html, body {
    width: 1200px; height: 1200px; overflow: hidden;
    background: var(--backdrop);
  }
  .stage { position: relative; width: 1200px; height: 1200px; }

  .card {
    position: absolute; left: 170px; width: 860px; height: 490px;
    border-radius: 4px;
    box-shadow: 0 18px 40px rgba(0,0,0,0.45);
    overflow: hidden;
  }
  .card--front { top: 90px; background: var(--card-green); }
  .card--back  { top: 620px; background: var(--card-cream); }

  /* brand lockup */
  .brand {
    position: absolute; display: flex; align-items: center; gap: 26px;
    font-family: "Poppins", sans-serif; font-weight: 300;
  }
  .brand__mark { flex: none; }
  .brand__text { display: flex; flex-direction: column; line-height: 1; }
  .brand__name { letter-spacing: 1px; }
  .brand__sub { text-transform: uppercase; }

  .card--front .brand { left: 50%; top: 50%; transform: translate(-50%, -50%); color: var(--card-green-ink); }
  .card--front .brand__name { font-size: 108px; }
  .card--front .brand__sub { font-size: 40px; letter-spacing: 22px; margin-top: 6px; padding-left: 4px; }

  .card--back .brand { left: 48px; top: 178px; color: var(--gold); gap: 16px; }
  .card--back .brand__name { font-size: 58px; }
  .card--back .brand__sub { font-size: 22px; letter-spacing: 11px; margin-top: 4px; padding-left: 2px; }

  .divider {
    position: absolute; left: 402px; top: 150px; width: 2px; height: 200px;
    background: var(--gold);
  }

  .contact-block {
    position: absolute; left: 428px; top: 160px; right: 30px;
    font-family: "Open Sans", sans-serif; color: var(--ink);
  }
  .person__name { font-size: 40px; font-weight: 800; letter-spacing: 0.5px; line-height: 1.1; white-space: nowrap; }
  .person__role { font-size: 17px; font-weight: 600; color: var(--gold); margin: 4px 0 14px; }
  .contact-list { list-style: none; display: flex; flex-direction: column; gap: 10px; }
  .contact-list li { display: flex; align-items: center; gap: 10px; font-size: 18px; font-weight: 600; white-space: nowrap; }
  .contact-icon {
    flex: none; width: 28px; height: 28px; border-radius: 50%;
    border: 1.5px solid var(--gold);
    display: flex; align-items: center; justify-content: center;
  }
</style>
</head>
<body>
<main class="stage">

  <section class="card card--front" aria-label="Card front">
    <div class="brand">
      <svg class="brand__mark" width="140" height="140" viewBox="0 0 140 140" aria-hidden="true">
        <circle cx="70" cy="70" r="66" fill="none" stroke="var(--card-green-ink)" stroke-width="3"/>
      </svg>
      <div class="brand__text">
        <span class="brand__name">veloran</span>
        <span class="brand__sub">Cabinets</span>
      </div>
    </div>
  </section>

  <section class="card card--back" aria-label="Card back">
    <div class="brand">
      <svg class="brand__mark" width="70" height="70" viewBox="0 0 70 70" aria-hidden="true">
        <circle cx="35" cy="35" r="33" fill="none" stroke="var(--gold)" stroke-width="2.5"/>
      </svg>
      <div class="brand__text">
        <span class="brand__name">veloran</span>
        <span class="brand__sub">Cabinets</span>
      </div>
    </div>

    <div class="divider"></div>

    <div class="contact-block">
      <h1 class="person__name">Mitchell Tarrowby</h1>
      <p class="person__role">Director Craftsman</p>
      <ul class="contact-list">
        <li>
          <span class="contact-icon">
            <svg width="16" height="12" viewBox="0 0 16 12" aria-hidden="true">
              <rect x="0.5" y="0.5" width="15" height="11" rx="1.5" fill="var(--gold)"/>
              <path d="M1 1.5 L8 7 L15 1.5" fill="none" stroke="#fff" stroke-width="1.3"/>
            </svg>
          </span>
          info@veloranjoinery-example.com.au
        </li>
        <li>
          <span class="contact-icon">
            <svg width="12" height="12" viewBox="0 0 12 12" aria-hidden="true">
              <circle cx="6" cy="6" r="5" fill="var(--gold)"/>
            </svg>
          </span>
          @veloran.cabinets/
        </li>
      </ul>
    </div>
  </section>

</main>
</body>
</html>
```